Pet sitting Business needs a website

We need a website that shows our services and prices. Shows our love of animals but also our professionalism. want a gallery, about, blog, services, links to fb and instagram accounts, newsletter archive. want it to be easy to access and wonderful to navigate. want the domain to be Birchfordpawhaven.com
take any info from FB site www.facebook.com/birchfordpawhaven
I would like it to fit square space platform

Target Market(s)

upscale area, responsible pet owners,

Industry/Entity Type

Pet Care

Coding

Coded - Design and coding required

Number of Pages Required

5+ page

Font styles to use
Sans Serif

Requirements
Must have
• (square space platform)
• Menu
• photo gallery
• about us
• services
• policies
• monthly newsletter
• unavailable dates
• Introduction (welcome)
• payment methods
• Daily updates
• testimonials (use from fb site)
Should not have
• stock photos

```html
<!DOCTYPE html>
<html lang="en">
<head>
<meta charset="utf-8">
<title>Birchford Paw Haven</title>
<link href="https://fonts.googleapis.com/css2?family=Roboto:wght@400;500;700&display=swap" rel="stylesheet">
<style>
:root{
  --blue:#0c7fb2;
  --blue-dark:#0a6d99;
  --orange:#e19a05;
  --text:#333;
  --muted:#666;
  --grey-bg:#efefef;
  --footer:#2c2c2c;
  --footer-bottom:#1b1b1b;
  --white:#fff;
}
*{box-sizing:border-box;margin:0;padding:0}
html,body{width:1200px;height:2423px;overflow:hidden}
body{position:relative;font-family:'Roboto',Arial,sans-serif;color:var(--text);background:var(--white)}
.abs{position:absolute}

/* header */
.hero-bg{left:0;top:0;width:1200px;height:735px;
  background:linear-gradient(180deg,#f7faf3 0%,#eef5e4 40%,#cfe3a8 70%,#b88a55 86%,#9a6a3a 100%)}
.join{left:90px;top:52px;font-size:19px;color:var(--blue)}
.phone{left:90px;top:80px;font-size:21px;color:#222;display:flex;align-items:center;gap:10px}
.brand{left:470px;top:40px;width:260px;text-align:center}
.brand .dot{display:inline-block;width:34px;height:34px;border-radius:50%;background:var(--orange);margin-bottom:6px}
.brand .name{font-size:26px;font-weight:500;color:var(--orange);line-height:1.1}
.social{right:90px;top:64px;display:flex;gap:10px}
.social span{width:20px;height:20px;background:var(--blue);border-radius:3px}

.nav{left:87px;top:147px;width:1026px;height:53px;background:var(--blue);display:flex}
.nav a{color:var(--white);text-decoration:none;font-size:14px;padding:0 12px;display:flex;align-items:center;height:100%;text-transform:uppercase}
.nav a.active{background:var(--orange);padding:0 20px}

.slider{left:92px;top:203px;width:1019px;height:508px;border:4px solid var(--white);
  box-shadow:0 4px 12px rgba(0,0,0,.3);
  background:linear-gradient(135deg,#c9ab82 0%,#a98962 45%,#8a6b48 100%)}
.slider .arrow{top:236px;width:28px;height:28px;border-radius:50%;background:rgba(0,0,0,.55)}
.slider .arrow.l{left:12px}.slider .arrow.r{right:12px}
.slide-title{right:36px;top:320px;text-align:right;color:var(--white)}
.slide-title h2{font-size:60px;font-weight:400}
.slide-title p{font-size:20px;font-weight:500;margin-top:6px}

/* welcome */
.welcome{left:0;top:735px;width:1200px;height:202px;text-align:center}
.sec-title{font-size:24px;font-weight:500;color:#222;text-transform:uppercase}
.sec-title em{font-style:normal;color:var(--orange)}
.welcome .sec-title{margin-top:50px}
.welcome p{width:820px;margin:16px auto 0;font-size:14px;line-height:23px;color:var(--muted)}

/* services */
.services{left:0;top:937px;width:1200px;height:584px;background:var(--grey-bg);text-align:center}
.services .sec-title{margin-top:52px}
.services .lead{margin-top:18px;font-size:14px;color:var(--muted)}
.card{top:140px;width:248px;height:352px;box-shadow:0 10px 10px -4px rgba(0,0,0,.25)}
.card .photo{height:215px}
.card .info{height:137px;color:var(--white);padding-top:18px}
.card h3{font-size:14px;font-weight:700;text-transform:uppercase}
.card p{font-size:11.5px;line-height:17px;margin-top:6px}
.card .btn{display:inline-block;margin-top:12px;background:#f4f4f4;color:#333;font-size:11px;padding:6px 24px;border-radius:3px}
.blue{background:var(--blue)}.orange{background:var(--orange)}

/* gallery + testimonials */
.gallery-title{left:87px;top:1572px;font-size:21px}
.thumb{width:200px;height:137px}
.testi-title{left:786px;top:1572px;font-size:21px;font-weight:500;color:var(--blue);text-transform:uppercase}
.quote{left:773px;top:1615px;width:337px;height:178px;background:var(--orange);border-radius:4px;color:var(--white);padding:24px 24px 0 24px;font-size:14px;line-height:27px}
.quote b{font-size:26px;margin-right:8px;vertical-align:-6px}
.quote-tail{left:1010px;top:1792px}
.avatar{left:772px;top:1813px;width:90px;height:90px;border-radius:50%;background:linear-gradient(135deg,#6b4a36,#c8a083)}
.author{left:890px;top:1825px;font-size:15px;color:#333}
.rule{left:890px;top:1857px;width:220px;height:1px;background:#e2e2e2}
.pager{left:892px;top:1872px;display:flex;gap:4px}
.pager span{width:22px;height:22px;border:1px solid #ddd;display:flex;align-items:center;justify-content:center;font-size:12px;color:#333}

/* newsletter */
.newsletter{left:0;top:1970px;width:1200px;height:147px;background:var(--blue);color:var(--white)}
.newsletter h4{position:absolute;left:148px;top:48px;font-size:26px;font-weight:500;text-transform:uppercase}
.newsletter small{position:absolute;left:148px;top:82px;font-size:16px}
.email{left:463px;top:43px;width:495px;height:60px;background:var(--white);color:#333;font-size:13px;padding:0 22px;display:flex;align-items:center}
.submit{left:969px;top:43px;width:144px;height:60px;background:linear-gradient(#f5f5f5,#d8d8d8);color:#333;font-size:20px;font-weight:500;border-radius:3px;display:flex;align-items:center;justify-content:center}

/* footer */
.footer{left:0;top:2117px;width:1200px;height:238px;background:var(--footer);color:#ddd}
.footer h5{position:absolute;top:56px;font-size:15px;font-weight:500;color:var(--white);text-transform:uppercase}
.footer .col{position:absolute;top:94px;font-size:11.5px;line-height:19px;color:#cfcfcf}
.footer ul{list-style:none}
.footer li{line-height:24px}
.footer li::before{content:"\25B8";margin-right:6px}
.foot-brand{left:900px;top:70px;width:230px;text-align:center}
.foot-brand .dot{display:inline-block;width:40px;height:40px;border-radius:50%;background:#8a8a8a}
.foot-brand .name{font-size:24px;color:#bdbdbd;margin-top:8px}
.copyright{left:0;top:2355px;width:1200px;height:68px;background:var(--footer-bottom);color:var(--white);font-size:12px;display:flex;align-items:center;justify-content:center}
</style>
</head>
<body>

<header>
  <div class="abs hero-bg" role="img" aria-label="Soft green meadow background with wooden deck"></div>
  <div class="abs join">Join the club today</div>
  <div class="abs phone">
    <svg width="16" height="16" viewBox="0 0 16 16"><rect width="16" height="16" rx="3" fill="#0c7fb2"/><path d="M5 3.5l2 2-1 1.2c.6 1.3 1.6 2.3 2.9 2.9l1.2-1 2 2-1.2 1.6C7.6 11.8 4.2 8.4 3.8 5z" fill="#fff"/></svg>
    210-555-0184
  </div>
  <div class="abs brand">
    <span class="dot"></span>
    <div class="name">Birchford Paw Haven</div>
  </div>
  <div class="abs social" aria-label="Social links"><span></span><span></span><span></span><span></span></div>

  <nav class="abs nav">
    <a class="active">Introduction</a><a>Photo Gallery</a><a>About Us</a><a>Services</a><a>Policies</a><a>Monthly Newsletter</a><a>Unavailable Dates</a><a>Payment Methods</a>
  </nav>

  <div class="abs slider" role="img" aria-label="Slide photo of a kitten and a white puppy cuddling">
    <span class="abs arrow l"></span><span class="abs arrow r"></span>
    <div class="abs slide-title"><h2>Pet Safety</h2><p>Birchford Paw Haven</p></div>
  </div>
</header>

<section class="abs welcome">
  <h1 class="sec-title">Welcome to <em>Birchford Paw Haven</em></h1>
  <p>Instead of feeling guilty when you must leave your pet for long work days, travel or appointments you can feel good knowing that you have provided your pet with a best friend, Birchford Paw Haven. Birchford Paw Haven provides your pet with one on one attention, plenty of play time and exercise and lots and lots of love until your return.</p>
</section>

<section class="abs services">
  <h2 class="sec-title">Our <em>Service</em></h2>
  <p class="lead">Lorem Ipsum has been the industry's standard dummy text ever since the 1500s, when an unknown printer took a galley</p>

  <div class="abs card" style="left:90px">
    <div class="photo" role="img" aria-label="Photo of a small chihuahua" style="background:linear-gradient(135deg,#d9d4cc,#8b7a68)"></div>
    <div class="info blue"><h3>Daily Visit - $25.00(per visit)</h3><p>No additional charge for each pet<br>Dog walks or play time for your pet</p><span class="btn">View More</span></div>
  </div>
  <div class="abs card" style="left:347px">
    <div class="photo" role="img" aria-label="Photo of a white cat on a rug" style="background:linear-gradient(135deg,#4a4642,#2b2826)"></div>
    <div class="info orange"><h3>Potty Visits - $10.00</h3><p>Usually done at noon and bedtime<br>letting them out to potty</p><span class="btn">View More</span></div>
  </div>
  <div class="abs card" style="left:606px">
    <div class="photo" role="img" aria-label="Photo of a fluffy small dog" style="background:linear-gradient(135deg,#a58b6e,#5f4a38)"></div>
    <div class="info blue"><h3>Dog Park</h3><p>30 min of play $40<br>(must be scheduled week in advance)</p><span class="btn">View More</span></div>
  </div>
  <div class="abs card" style="left:862px">
    <div class="photo" role="img" aria-label="Photo of three dogs on leashes" style="background:linear-gradient(135deg,#8d8d88,#3e3b37)"></div>
    <div class="info orange"><h3>Just Walks</h3><p>$15.00/ 20 min walk<br>Vet appointment visit</p><span class="btn">View More</span></div>
  </div>
</section>

<section>
  <h2 class="abs sec-title gallery-title">Photo <em>Gallery</em></h2>
  <div class="abs thumb" style="left:87px;top:1617px;background:linear-gradient(135deg,#9c7f6a,#4c3a30)" role="img" aria-label="Owner holding a puppy"></div>
  <div class="abs thumb" style="left:297px;top:1617px;background:linear-gradient(135deg,#b08a5f,#5a4a3c)" role="img" aria-label="Golden dog on a porch"></div>
  <div class="abs thumb" style="left:507px;top:1617px;background:linear-gradient(135deg,#c99a6e,#5d4430)" role="img" aria-label="Owner with an orange cat"></div>
  <div class="abs thumb" style="left:87px;top:1764px;background:linear-gradient(135deg,#cfcac0,#5a5a52)" role="img" aria-label="Three dogs in a yard"></div>
  <div class="abs thumb" style="left:297px;top:1764px;background:linear-gradient(135deg,#5e7a45,#2f3f24)" role="img" aria-label="White dog playing in a garden"></div>
  <div class="abs thumb" style="left:507px;top:1764px;background:linear-gradient(135deg,#6d665c,#2c2a26)" role="img" aria-label="Two small dogs behind a gate"></div>

  <h2 class="abs testi-title">Testimonials</h2>
  <div class="abs quote"><b>&ldquo;</b>Lorem ipsum dolor sit amet, consectetur adipiscing elit, sed do eiusmod tempor incididunt ut labore et dolore magna aliqua. Ut enim ad minim veniam, quis nostrud exercitation Lorem ipsum dolor sit amet,</div>
  <svg class="abs quote-tail" width="32" height="26" viewBox="0 0 32 26"><path d="M0 0h32L28 26z" fill="#e19a05"/></svg>
  <div class="abs avatar" role="img" aria-label="Client portrait"></div>
  <div class="abs author">John Doe -&nbsp; Parents Education</div>
  <div class="abs rule"></div>
  <div class="abs pager"><span>&lsaquo;</span><span>&rsaquo;</span></div>
</section>

<section class="abs newsletter">
  <svg class="abs" style="left:86px;top:50px" width="50" height="44" viewBox="0 0 50 44"><path d="M4 16L38 2l8 26-34 14z" fill="#fff"/><path d="M4 16l22 8 20-22" fill="none" stroke="#0c7fb2" stroke-width="2"/></svg>
  <h4>Monthly Newsletter</h4>
  <small>Neque porro quisquam est qui dolorem</small>
  <div class="abs email">EMAIL ID</div>
  <div class="abs submit">SUBMIT</div>
</section>

<footer class="abs footer">
  <h5 style="left:90px">Text Widget</h5>
  <div class="col" style="left:90px;width:280px">NestPress helps you to quickly and easily build incredible websites with a site builder.<br><br>Proin gravida nibh vel velit auctor aliquet. Aenean sollicitudin, lorem quis bibendum auctor, nisi elit consequat ipsum, nec sagittis.</div>
  <h5 style="left:420px">Links</h5>
  <ul class="col" style="left:420px;top:88px"><li>Customer Support</li><li>Documentation</li><li>Resources</li><li>General FAQs</li><li>Shortcodes</li></ul>
  <h5 style="left:628px">Get in Touch</h5>
  <div class="col" style="left:628px">Address : 1420 Linden Row Ave,<br>Birchford, NJ<br><br>Phone : 210-555-0184<br><br>Email : hello@birchfordpawhaven.com</div>
  <div class="abs foot-brand"><span class="dot"></span><div class="name">Birchford Paw Haven</div></div>
</footer>
<div class="abs copyright">Copyright &copy; 2016. All Rights Reserved</div>

</body>
</html>
```